Give Gold Kite an Online Presence!

Gold Kite Property Maintenance is an Australian Owned property maintenance company who needs a stand out online presence.

GK maintains many buildings and sites and wants to appeal to a corporate professional market with their brand new website. GK is essentially a handyman service offering all maintenance services to home owners, office managers, real estate agents and strata managers.

The Website:
We need a corporate website that appeals to our broader customer base (property owners, property managers, office managers) the copy is being written by a professional so use filler text for now.

Things that we want:
Home page that sets us apart and appeals to the corporate and residential market. The home page needs to not focus on either the residential or commercial market. The home page should focus on our logo and branding. We have a logo already and it is attached to the brief, please use it and try to consider the colour pallette that goes with it. Whilst we want the site to appear strong and manly it is important to remember that 95% of our customers are female so we need the site to be appealing to women. Women need to believe that we are strong, dependable and trustworthy.
We'd like a quote page and potentially also the ability to get a quote from the home page (please don't put it in if it ruins the overall feel of the home page)
An "about us" page
A contact us page
A blog that's built in (we don't want to link to an external blog)
(overall we'd expect to have 6 or 7 pages total)

The site will also need coding - we expect this to be done in a separate project but need you to consider a few things about the coding side of things.

It needs to be iPhone and iPad compatible.

We'd like you to suggest the best CMS that you would use or if you would suggest not using a CMS please let us know with your submissions.

Target Market(s)

Property owners, office managers and property managers who need maintenance on buildings (So all of them)

Industry/Entity Type

Property Maintenance

Requirements
Must have
• Our Logo
Home page
About Us
Residential
Commercial
Real Estate/Strata
Contact Us/Quote
Blog
Nice to have
• Quote form included in home page
Movement on the home page at least
Should not have
• other logos, too much colour
NO FLASH

```html
<!DOCTYPE html>
<html lang="en">
<head>
<meta charset="utf-8">
<title>Gold Kite Property Maintenance</title>
<link href="https://fonts.googleapis.com/css2?family=Baloo+2:wght@600&family=Ubuntu:wght@300;400&display=swap" rel="stylesheet">
<style>
:root{
  --orange:#ff6a00;
  --orange-light:#ff9a3c;
  --ink:#222;
  --text:#4a4a4a;
  --line:#d6d6d6;
  --panel-border:#e2e2e2;
  --footer:#2f2f2f;
  --footer-dark:#1f1f1f;
  --footer-text:#e8e8e8;
  --footer-head:#9a9a9a;
  --field-dark:#141414;
  --social:#8c8c8c;
  --white:#fff;
}
*{box-sizing:border-box;margin:0;padding:0}
html,body{width:1057px;height:1200px;overflow:hidden;background:var(--white)}
body{position:relative;font-family:"Ubuntu",sans-serif;color:var(--text)}
.abs{position:absolute}
/* header */
.brand{left:72px;top:22px;display:flex;align-items:center;gap:8px}
.brand-mark{width:22px;height:22px;background:var(--orange)}
.brand-name{font-family:"Ubuntu",sans-serif;font-size:17px;font-weight:400;color:var(--ink)}
.social{top:18px;display:flex;gap:6px;left:907px}
.social span{width:33px;height:33px;border-radius:5px;display:block;background:var(--social)}
.search{left:705px;top:68px;width:276px;height:28px;border:1px solid #bbb;border-radius:8px;box-shadow:inset 0 2px 3px rgba(0,0,0,.12);font-size:14px;color:var(--ink);padding:4px 13px;display:flex;justify-content:space-between;align-items:center}
.nav{left:0;top:112px;width:1057px;height:42px;border-top:2px solid var(--line);border-bottom:2px solid var(--line)}
.nav ul{list-style:none;position:relative;height:100%}
.nav li{position:absolute;top:9px;font-size:14px;color:var(--ink);height:24px;line-height:24px}
.nav .sep{position:absolute;top:7px;width:1px;height:27px;background:#555}
.nav .home{left:84px;width:59px;text-align:center;color:var(--white);background:linear-gradient(var(--orange-light),var(--orange));border-radius:4px;top:8px;height:25px}
/* slider */
.slide{left:75px;top:169px;width:906px;height:366px;border-radius:8px;background:linear-gradient(100deg,#b9b19a 0%,#93a595 35%,#8fa7a2 60%,#6b7f92 85%,#a08070 100%)}
.arrow{top:330px;width:16px;height:38px}
/* panels */
.panel{top:560px;width:279px;height:277px;border:1px solid var(--panel-border);border-radius:4px;background:var(--white)}
.panel h2{position:absolute;left:8px;top:9px;width:263px;height:32px;border-radius:6px;background:linear-gradient(var(--orange-light),var(--orange) 70%);color:var(--white);font-family:"Baloo 2",sans-serif;font-weight:600;font-size:22px;line-height:36px;padding-left:19px;letter-spacing:.2px}
.about-text{position:absolute;left:26px;top:57px;width:231px;font-size:12px;line-height:16px;text-align:justify;font-weight:300;color:#333}
.about-text p+p{margin-top:16px}
.services{position:absolute;left:35px;top:54px;list-style:none;font-size:12px;font-weight:300;color:#333}
.services li{height:26.5px;display:flex;align-items:center;gap:6px}
.btn{position:absolute;right:9px;bottom:11px;width:86px;height:25px;border-radius:4px;background:linear-gradient(#3a3a3a,#0b0b0b);color:var(--white);font-size:12px;text-align:center;line-height:25px}
.field{position:absolute;left:17px;width:249px;border:1px solid #ccc;border-radius:5px;font-size:12px;color:#777;padding:8px 12px;font-weight:300}
/* footer */
.footer{left:0;top:864px;width:1057px;height:286px;background:radial-gradient(ellipse at 50% 0,#3d3d3d,var(--footer) 70%)}
.footer h3{position:absolute;top:33px;font-size:15px;font-weight:400;color:var(--footer-head);letter-spacing:.2px}
.vline{position:absolute;top:33px;width:1px;height:230px;background:#555}
.widget{position:absolute;left:75px;top:73px;list-style:none;font-size:12px;color:var(--footer-text);font-weight:300}
.widget li{height:26.5px;display:flex;align-items:center;gap:12px}
.widget li::before{content:"";width:4px;height:4px;border-radius:50%;background:var(--footer-text)}
.post{position:absolute;left:271px;display:flex;gap:10px}
.thumb{width:50px;height:50px;border-radius:6px;flex:none}
.post p{width:126px;font-size:9px;line-height:16px;color:var(--footer-text);text-align:justify;font-weight:300;letter-spacing:-.1px}
.address{position:absolute;left:494px;top:64px;font-size:11.5px;line-height:16px;color:var(--footer-text);font-weight:300}
.phone{position:absolute;left:590px;top:96px;font-size:11.5px;line-height:16px;color:var(--footer-text);font-weight:300}
.map{position:absolute;left:494px;top:138px;width:175px;height:120px;border-radius:3px;background:linear-gradient(135deg,#e7dfb4,#cfd7b2 50%,#c9c9c0)}
.dfield{position:absolute;left:739px;width:236px;background:var(--field-dark);border:1px solid #444;border-radius:5px;font-size:13px;color:#999;padding:6px 11px;font-weight:300}
.bottom{left:0;top:1150px;width:1057px;height:50px;background:var(--footer-dark);text-align:center;font-size:10px;line-height:50px;color:var(--footer-text);font-weight:300}
</style>
</head>
<body>
<header>
  <div class="abs brand"><span class="brand-mark"></span><span class="brand-name">Gold Kite</span></div>
  <div class="abs social" role="img" aria-label="Social media links"><span></span><span></span></div>
  <div class="abs search">Search
    <svg width="12" height="12" viewBox="0 0 12 12"><circle cx="7" cy="5" r="3.5" fill="none" stroke="#3a6fb0" stroke-width="1.5"/><line x1="4.5" y1="7.5" x2="1" y2="11" stroke="#3a6fb0" stroke-width="1.8"/></svg>
  </div>
  <nav class="abs nav">
    <ul>
      <li class="home">Home</li>
      <li class="sep" style="left:158px"></li>
      <li style="left:195px">About Us</li>
      <li class="sep" style="left:277px"></li>
      <li style="left:312px">Residential</li>
      <li class="sep" style="left:405px"></li>
      <li style="left:440px">Commercial</li>
      <li class="sep" style="left:536px"></li>
      <li style="left:572px">Real Estate/Strata</li>
      <li class="sep" style="left:704px"></li>
      <li style="left:739px">Contact Us/Quote</li>
      <li class="sep" style="left:872px"></li>
      <li style="left:909px">Blog</li>
    </ul>
  </nav>
</header>

<section>
  <svg class="abs arrow" style="left:36px" viewBox="0 0 16 38"><polyline points="13,2 3,19 13,36" fill="none" stroke="#555" stroke-width="2"/></svg>
  <div class="abs slide" role="img" aria-label="Photo of a cleaner wiping a mirror"></div>
  <svg class="abs arrow" style="left:997px" viewBox="0 0 16 38"><polyline points="3,2 13,19 3,36" fill="none" stroke="#555" stroke-width="2"/></svg>
</section>

<section>
  <article class="abs panel" style="left:73px">
    <h2>about us</h2>
    <div class="about-text">
      <p>Lorem Ipsum is simply dummy text of the printing and typesetting industry. Lorem Ipsum has been the industry's standard dummy text ever since the 1500s.</p>
      <p>Lorem Ipsum is simply dummy text of the printing and typesetting industry. Lorem Ipsum has been the industry's standard dummy text ever since the 1500s. Lorem Ipsum is simply dummy textprinting and typesetting industry.</p>
    </div>
    <span class="btn">Read More</span>
  </article>
  <article class="abs panel" style="left:387px">
    <h2>our services</h2>
    <ul class="services">
      <li>&#10132; Lorem Ipsum is simply dummy text</li>
      <li>&#10132; Lorem Ipsum is simply dummy text</li>
      <li>&#10132; Lorem Ipsum is simply dummy text</li>
      <li>&#10132; Lorem Ipsum is simply dummy text</li>
      <li>&#10132; Lorem Ipsum is simply dummy text</li>
      <li>&#10132; Lorem Ipsum is simply dummy text</li>
      <li>&#10132; Lorem Ipsum is simply dummy text</li>
    </ul>
    <span class="btn">Read More</span>
  </article>
  <article class="abs panel" style="left:701px">
    <h2>quick quote form</h2>
    <div class="field" style="top:54px">Name</div>
    <div class="field" style="top:98px">Email</div>
    <div class="field" style="top:140px;height:93px">Message</div>
    <span class="btn">Read More</span>
  </article>
</section>

<footer class="abs footer">
  <h3 style="left:75px">FOOTER WIDGET</h3>
  <span class="vline" style="left:250px"></span>
  <ul class="widget">
    <li>Lorem Ipsum Dolor Sit Amet</li><li>Lorem Ipsum Dolor Sit Amet</li><li>Lorem Ipsum Dolor Sit Amet</li><li>Lorem Ipsum Dolor Sit Amet</li><li>Lorem Ipsum Dolor Sit Amet</li><li>Lorem Ipsum Dolor Sit Amet</li><li>Lorem Ipsum Dolor Sit Amet</li>
  </ul>
  <h3 style="left:270px">BLOG POSTS</h3>
  <div class="post" style="top:71px"><span class="thumb" role="img" aria-label="Blog post photo" style="background:linear-gradient(135deg,#9ab4cf,#e3c9a3)"></span><p>Lorem Ipsum is simply dummy text of the printing and typesetting industry.</p></div>
  <div class="post" style="top:133px"><span class="thumb" role="img" aria-label="Blog post photo" style="background:linear-gradient(135deg,#c9c2b8,#e6d7c5)"></span><p>Lorem Ipsum is simply dummy text of the printing and typesetting industry.</p></div>
  <div class="post" style="top:197px"><span class="thumb" role="img" aria-label="Blog post photo" style="background:linear-gradient(135deg,#e0b66e,#f1d9ae)"></span><p>Lorem Ipsum is simply dummy text of the printing and typesetting industry.</p></div>
  <span class="vline" style="left:470px"></span>
  <h3 style="left:494px">LOCATION MAP</h3>
  <div class="address">Door No, XXX Street,<br>YYY Street,<br>City Name,<br>Pincode,</div>
  <div class="phone">Phone: (XXX) XXX XXXX<br>Fax: (XXX) XXX XXXX</div>
  <div class="map" role="img" aria-label="Street map of the office location"></div>
  <span class="vline" style="left:722px"></span>
  <h3 style="left:739px">CONTACT US</h3>
  <div class="dfield" style="top:66px;height:31px">Name</div>
  <div class="dfield" style="top:114px;height:31px">Email</div>
  <div class="dfield" style="top:162px;height:57px">Message</div>
</footer>
<div class="abs bottom">Copyrights &copy; 2012. All Rights Reserved.</div>
</body>
</html>
```